Mental Health care Company in Washington DC

We are a new mental health care services provider in Washington DC. Please look at these sites.
https://brightwaterfamilysupport.com
https://www.quietharborinc.com
https://willowgate-dc.org/
https://www.tidepathdc.com
https://www.thelanternofdc.com

```html
<!DOCTYPE html>
<html lang="en">
<head>
<meta charset="utf-8">
<title>Cedarline Health Services – Mental Wellness for Washington, D.C.</title>
<link rel="stylesheet" href="https://fonts.googleapis.com/css2?family=Poppins:ital,wght@0,400;0,500;0,600;1,400&family=Lato:wght@400;700&display=swap">
<style>
:root{
  --teal:#a2dade;
  --orange:#f58a2e;
  --navy:#0d2145;
  --ink:#12213f;
  --body:#3a3f4a;
  --white:#ffffff;
  --line:#c9ccd3;
}
*{box-sizing:border-box;margin:0;padding:0}
html,body{width:1200px;height:3818px;overflow:hidden}
body{position:relative;font-family:"Lato",sans-serif;color:var(--body);background:var(--white)}
.abs{position:absolute}
.heading{font-family:"Poppins",sans-serif;color:var(--ink);font-weight:600}
.kicker{font-family:"Poppins",sans-serif;font-style:italic;font-size:23px;color:var(--ink)}
.btn{position:absolute;display:flex;align-items:center;justify-content:center;font-family:"Poppins",sans-serif;font-weight:600;border-radius:5px}
.btn-orange{background:var(--orange);color:var(--white)}
.btn-navy{background:var(--navy);color:var(--white)}

.topbar{left:0;top:0;width:1200px;height:43px;background:var(--teal);font-family:"Poppins",sans-serif;font-size:15px;color:var(--ink)}
.topbar span{position:absolute;top:11px}
.topbar svg{position:absolute}

.nav{left:0;top:43px;width:1200px;height:86px;background:var(--white)}
.brand{position:absolute;left:112px;top:24px;display:flex;align-items:center;gap:9px;font-family:"Poppins",sans-serif;font-weight:500;font-size:26px;color:var(--ink);white-space:nowrap}
.brand .dot{width:12px;height:12px;border-radius:50%;background:var(--orange)}
.menu{position:absolute;top:30px;font-family:"Poppins",sans-serif;font-size:15px;color:var(--ink)}
.menu.active{color:var(--orange)}
.active-bar{position:absolute;left:387px;top:120px;width:52px;height:5px;background:var(--orange)}

.hero{left:0;top:129px;width:1200px;height:555px;background:linear-gradient(100deg,#5a6e78 0%,#7d8f95 30%,#b19a82 55%,#8aa4ae 75%,#6d8794 100%)}
.hero-title{position:absolute;left:112px;top:96px;font-family:"Poppins",sans-serif;font-weight:600;font-size:51px;line-height:68px;color:var(--white)}
.hero-title .mark{background:var(--orange);padding:0 8px}
.hero-lede{position:absolute;left:112px;top:240px;width:470px;font-size:16px;line-height:29px;color:var(--white)}
.hero-btn{position:absolute;left:110px;top:322px;width:204px;height:50px;border:2px solid var(--white);border-radius:8px;display:flex;align-items:center;justify-content:center;font-family:"Poppins",sans-serif;font-weight:600;font-size:15px;color:var(--white)}

.services{left:0;top:684px;width:1200px;height:590px;background:linear-gradient(180deg,#a3dbe0,#97d1d6)}
.svc-item{position:absolute;top:188px;width:232px;text-align:center}
.svc-photo{width:232px;height:232px;border-radius:50%}
.svc-name{margin-top:28px;font-family:"Poppins",sans-serif;font-weight:500;font-size:19px;line-height:30px;color:var(--ink)}
.svc-overlay{position:absolute;left:0;top:0;width:232px;height:232px;border-radius:50%;border:3px solid var(--white);background:rgba(245,138,46,.85);display:flex;align-items:center;justify-content:center;padding:0 32px;color:var(--white);font-size:14px;line-height:27px}
.arrow{position:absolute;top:292px;width:30px;height:30px}

.welcome{left:0;top:1274px;width:1200px;height:470px;text-align:center}

.mv{left:0;top:1744px;width:1200px;height:313px;overflow:hidden}
.mv-text{position:absolute;font-size:14.5px;line-height:27px}

.badge{position:absolute;top:2250px;width:200px;height:200px;border-radius:50%}

.form-card{left:156px;top:2801px;width:889px;height:474px;background:var(--white);border-radius:6px}
.field{position:absolute;border-bottom:1px solid var(--line);font-family:"Poppins",sans-serif;font-size:14px;color:#555;padding-left:12px}

.foot-line{position:absolute;height:2px;background:#8c97ad}
.contact-icon{position:absolute;width:64px;height:64px;border-radius:50%;background:var(--white);display:flex;align-items:center;justify-content:center}
.contact-label{position:absolute;font-family:"Poppins",sans-serif;font-weight:500;font-size:17px;color:var(--white)}
.contact-value{position:absolute;font-family:"Poppins",sans-serif;font-size:15px;line-height:26px;color:var(--white)}
.foot-link{position:absolute;top:3700px;font-family:"Poppins",sans-serif;font-size:13.5px;color:var(--white)}
</style>
</head>
<body>

<div class="abs topbar">
  <svg style="left:110px;top:8px" width="27" height="27" viewBox="0 0 24 24" fill="none" stroke="#12213f" stroke-width="1.6"><circle cx="12" cy="12" r="10"/><path d="M12 6v6l4 2"/></svg>
  <span style="left:147px">Hours: Mon - Sat 8.30AM&nbsp; - 5.00PM</span>
  <svg style="left:436px;top:10px" width="21" height="21" viewBox="0 0 24 24" fill="#12213f"><path d="M6.6 10.8a15 15 0 0 0 6.6 6.6l2.2-2.2a1 1 0 0 1 1-.25 11.4 11.4 0 0 0 3.6.57 1 1 0 0 1 1 1V20a1 1 0 0 1-1 1A17 17 0 0 1 3 4a1 1 0 0 1 1-1h3.5a1 1 0 0 1 1 1c0 1.25.2 2.45.57 3.57a1 1 0 0 1-.25 1z"/></svg>
  <span style="left:467px">24/7 Help +1 (202) 555-0147</span>
  <svg style="left:978px;top:9px" width="26" height="26" viewBox="0 0 26 26"><circle cx="13" cy="13" r="12" fill="#2a3f8f"/><path d="M2 13h22M13 2v22" stroke="#fff" stroke-width="5"/><path d="M2 13h22M13 2v22" stroke="#d0283a" stroke-width="2.5"/></svg>
  <span style="left:1014px;font-weight:500">English</span>
  <svg style="left:1076px;top:17px" width="12" height="9" viewBox="0 0 12 9"><path d="M0 0h12L6 9z" fill="#12213f"/></svg>
</div>

<header class="abs nav">
  <div class="brand"><span class="dot"></span>Cedarline Health</div>
  <span class="menu active" style="left:391px">Home</span>
  <span class="menu" style="left:463px">Our Services</span>
  <span class="menu" style="left:584px">Insurance</span>
  <span class="menu" style="left:688px">About</span>
  <span class="menu" style="left:762px">Contact</span>
  <div class="btn btn-orange" style="left:861px;top:19px;width:228px;height:47px;font-size:15px;border-radius:6px">Make An Appointment</div>
</header>
<div class="active-bar"></div>

<section class="abs hero" role="img" aria-label="Woman with closed eyes breathing calmly beside a window overlooking a city skyline">
  <h1 class="hero-title"><span class="mark">Mental Wellness</span> for<br>Washington, D.C.</h1>
  <p class="hero-lede">Empowering individuals and families with accessible, culturally competent mental health care — in-person and online.</p>
  <div class="hero-btn">Start Your Journey</div>
</section>

<section class="abs services">
  <div class="kicker abs" style="left:116px;top:74px">What We Do</div>
  <h2 class="heading abs" style="left:116px;top:112px;font-size:37px">Our Services</h2>
  <p class="abs" style="left:470px;top:100px;width:600px;font-size:14px;line-height:28px;color:#6f8a8f">Lorem Ipsum is simply dummy text of the printing and typesetting industry. Lorem Ipsum has been the industry's standard dummy text ever since the 1500</p>

  <svg class="arrow" style="left:40px" viewBox="0 0 30 30" fill="none" stroke="#12213f" stroke-width="1.6"><circle cx="15" cy="15" r="13.5"/><path d="M21 15H9M13 11l-4 4 4 4"/></svg>
  <svg class="arrow" style="left:1131px" viewBox="0 0 30 30" fill="none" stroke="#12213f" stroke-width="1.6"><circle cx="15" cy="15" r="13.5"/><path d="M9 15h12M17 11l4 4-4 4"/></svg>

  <div class="svc-item" style="left:113px">
    <div class="svc-photo" role="img" aria-label="Therapist taking notes with a distressed client" style="background:linear-gradient(135deg,#6b5a52,#c9b4a8 55%,#9a7c6c)"></div>
    <div class="svc-name">Individual Therapy</div>
  </div>
  <div class="svc-item" style="left:359px">
    <div class="svc-photo" role="img" aria-label="Pharmacist writing a prescription beside a medicine bottle" style="background:linear-gradient(135deg,#e8e2dc,#c79b7a)"></div>
    <div class="svc-overlay">Lorem Ipsum is simply dummy text of the printing and typesetting industry.</div>
    <div class="svc-name">Medication<br>Management</div>
  </div>
  <div class="svc-item" style="left:607px">
    <div class="svc-photo" role="img" aria-label="Psychiatrist with a clipboard talking with a patient" style="background:linear-gradient(135deg,#7a6a5a,#b9b2a8 50%,#4e5660)"></div>
    <div class="svc-name">Psychiatry</div>
  </div>
  <div class="svc-item" style="left:854px">
    <div class="svc-photo" role="img" aria-label="Woman speaking to a community support group" style="background:linear-gradient(135deg,#8f7760,#d2b59a 50%,#5a4d44)"></div>
    <div class="svc-name">Community Support<br>Services</div>
  </div>
</section>

<section class="abs welcome">
  <div class="kicker" style="margin-top:88px">Welcome To</div>
  <h2 class="heading" style="font-size:37px;margin-top:4px">Cedarline Health Services</h2>
  <div style="width:110px;height:4px;background:var(--orange);margin:16px auto 0;border-radius:2px"></div>
  <p style="width:830px;margin:28px auto 0;font-size:14.5px;line-height:27px">Lorem Ipsum is simply dummy text of the printing and typesetting industry. Lorem Ipsum has been the industry's standard dummy text ever since the 1500s, when an unknown printer took a galley of type and scrambled it to make a type specimen book. It has survived not only five centuries, but also the leap into electronic typesetting, remaining essentially unchanged.</p>
  <div class="btn btn-orange" style="left:487px;top:332px;width:227px;height:47px;font-size:15px">Make An Appointment</div>
</section>

<section class="abs mv">
  <div class="abs" role="img" aria-label="Soft teal illustration of a tree and silhouette" style="left:0;top:0;width:1200px;height:313px;background:linear-gradient(120deg,#a6dce0,#8ccbd1)"></div>
  <svg class="abs" style="left:0;top:0" width="1200" height="313" viewBox="0 0 1200 313" role="img" aria-label="Team members in a warm orange tone">
    <polygon points="632,0 1200,0 1200,313 566,313" fill="#f48a32"/>
  </svg>
  <h2 class="heading abs" style="left:32px;top:66px;font-size:37px">Our Mission</h2>
  <p class="mv-text abs" style="left:32px;top:130px;width:510px">Lorem Ipsum is simply dummy text of the printing and typesetting industry. Lorem Ipsum has been the industry's standard dummy text ever since the 1500s,</p>
  <div class="btn btn-navy" style="left:32px;top:202px;width:123px;height:43px;font-size:14px">Read More</div>

  <div class="abs" style="left:551px;top:99px;width:93px;height:93px;border-radius:50%;background:var(--white)"></div>

  <h2 class="heading abs" style="left:667px;top:66px;font-size:37px;color:var(--white)">Our Vision</h2>
  <p class="mv-text abs" style="left:667px;top:130px;width:520px;color:var(--white)">Lorem Ipsum is simply dummy text of the printing and typesetting industry. Lorem Ipsum has been the industry's standard dummy text ever since the 1500s,</p>
  <div class="btn btn-navy" style="left:667px;top:202px;width:123px;height:43px;font-size:14px">Read More</div>
</section>

<section>
  <div class="kicker abs" style="left:0;top:2128px;width:1200px;text-align:center">Our Certifications</div>
  <h2 class="heading abs" style="left:0;top:2168px;width:1200px;text-align:center;font-size:37px">Accredited. Trusted. Committed to Excellence.</h2>
  <div class="badge" style="left:219px;background:#c9a64a;box-shadow:inset 0 0 0 14px #e6c86a"></div>
  <div class="badge" style="left:500px;background:#f2793a;box-shadow:inset 0 0 0 14px #fff,inset 0 0 0 18px #f2793a"></div>
  <div class="badge" style="left:776px;background:#2b2414;box-shadow:inset 0 0 0 12px #d7b24a"></div>
</section>

<div class="abs" role="img" aria-label="Close-up of hands comforting another person's hands" style="left:0;top:2546px;width:1200px;height:524px;background:linear-gradient(120deg,#3b2a22,#6c5240 45%,#4d5038 80%,#2f2a22)"></div>
<div class="abs" style="left:0;top:3070px;width:1200px;height:748px;background:var(--navy)"></div>

<section class="abs form-card">
  <h2 class="heading" style="text-align:center;font-size:37px;line-height:47px;margin-top:51px">Request A<br>Free Consultation</h2>
  <div class="field" style="left:70px;top:189px;width:356px;height:30px">Name</div>
  <div class="field" style="left:463px;top:189px;width:356px;height:30px">Name</div>
  <div class="field" style="left:70px;top:262px;width:356px;height:30px">Contact Number</div>
  <div class="field" style="left:463px;top:262px;width:356px;height:30px">Email Address</div>
  <div class="field" style="left:70px;top:334px;width:749px;height:72px">your Message</div>
</section>
<div class="btn btn-orange" style="left:488px;top:3254px;width:227px;height:47px;font-size:15px">Make An Appointment</div>

<footer>
  <div class="abs" style="left:0;top:3400px;width:1200px;display:flex;justify-content:center;align-items:center;gap:12px;font-family:'Poppins',sans-serif;font-weight:500;font-size:44px;color:var(--white)"><span style="width:16px;height:16px;border-radius:50%;background:var(--orange)"></span>Cedarline Health</div>

  <div class="foot-line" style="left:121px;top:3512px;width:957px"></div>

  <div class="contact-icon" style="left:162px;top:3560px"><svg width="30" height="30" viewBox="0 0 24 24" fill="#0d2145"><path d="M12 2a7 7 0 0 0-7 7c0 5.2 7 13 7 13s7-7.8 7-13a7 7 0 0 0-7-7zm0 9.5A2.5 2.5 0 1 1 12 6.5a2.5 2.5 0 0 1 0 5z"/></svg></div>
  <div class="contact-label" style="left:243px;top:3546px">Address</div>
  <div class="contact-value" style="left:243px;top:3572px">Lorem Ipsum is simply<br>dummy text</div>
  <div class="abs" style="left:470px;top:3554px;width:2px;height:80px;background:#8c97ad"></div>

  <div class="contact-icon" style="left:502px;top:3560px"><svg width="28" height="28" viewBox="0 0 24 24" fill="#0d2145"><path d="M6.6 10.8a15 15 0 0 0 6.6 6.6l2.2-2.2a1 1 0 0 1 1-.25 11.4 11.4 0 0 0 3.6.57 1 1 0 0 1 1 1V20a1 1 0 0 1-1 1A17 17 0 0 1 3 4a1 1 0 0 1 1-1h3.5a1 1 0 0 1 1 1c0 1.25.2 2.45.57 3.57a1 1 0 0 1-.25 1z"/></svg></div>
  <div class="contact-label" style="left:585px;top:3558px">Phone</div>
  <div class="contact-value" style="left:585px;top:3584px">+1 (202) 555-0147</div>
  <div class="abs" style="left:755px;top:3554px;width:2px;height:80px;background:#8c97ad"></div>

  <div class="contact-icon" style="left:786px;top:3560px"><svg width="32" height="32" viewBox="0 0 24 24" fill="none" stroke="#0d2145" stroke-width="1.8"><rect x="3" y="5" width="18" height="14" rx="1.5"/><path d="M3 6l9 7 9-7M3 18l7-6M21 18l-7-6"/></svg></div>
  <div class="contact-label" style="left:873px;top:3558px">Email Address</div>
  <div class="contact-value" style="left:873px;top:3584px">info@cedarlinehealth.com</div>

  <div class="foot-line" style="left:121px;top:3654px;width:957px"></div>

  <span class="foot-link" style="left:303px">HOME</span>
  <span class="foot-link" style="left:400px">ABOUT US</span>
  <span class="foot-link" style="left:521px">OUR SERVICES</span>
  <span class="foot-link" style="left:675px">INSURANCE</span>
  <span class="foot-link" style="left:810px">CONTACT US</span>

  <div class="foot-line" style="left:110px;top:3746px;width:978px"></div>
  <div class="abs" style="left:0;top:3772px;width:1200px;text-align:center;font-family:'Poppins',sans-serif;font-size:14px;color:var(--white)">Copyright © 2025 Cedarline Health | All Rights Reserved</div>
</footer>

</body>
</html>
```